IT Company that provides secure IT solutions and services to our customers

We need business cards and a logo for a new IT Solutions company just created based in Kuala Lumpur, Malaysia. But will also be serving other countries in the region. We provide secure data, voice solutions on mobile platforms. Our first offering is encrypted voice and data solutions for IOS, Android, Windows and BlackBerry devices.

Target Market(s)

large organizations Govt, Police, Defence, Anti-corruption, Legal, highly regulated industries such as Health-care, Financial, Banking, Insurance,

Industry/Entity Type

Information Technology

Contact Information for Business Card

VelmoraNet (Logo - colour is ORVEX blue)Roshan Adeel Managing Director Kryption IT Sdn. Bhd.5th Floor, Block D, Wisma PLB,No.14 Jalan Seri Melor,50470, Kuala LumpurMalaysia

Font styles to use
Sans Serif

Colors
3176b5
ec1f27
fbed22

Requirements
Must have
• VelmoraNet all in Blue like ORVEX blue. A logo design perhaps a play of VN, K with a dangling T (colour can be any)
Nice to have
• I want a clean crisp card, not too busy, easy to read.

```html
<!DOCTYPE html>
<html lang="en">
<head>
<meta charset="utf-8">
<title>VelmoraNet Business Card</title>
<link href="https://fonts.googleapis.com/css2?family=Arimo:wght@400;700&display=swap" rel="stylesheet">
<style>
  :root {
    --backdrop: #b9b8bd;
    --card: #efeeec;
    --ink: #1f2430;
    --ink-soft: #3a3f4a;
  }
  * { margin: 0; padding: 0; box-sizing: border-box; }
  html, body {
    width: 1200px;
    height: 1000px;
    overflow: hidden;
    background: var(--backdrop);
  }
  .sheet {
    position: relative;
    width: 1200px;
    height: 1000px;
    display: flex;
    flex-direction: column;
    align-items: center;
    justify-content: center;
    gap: 24px;
  }
  .card {
    position: relative;
    width: 820px;
    height: 468px;
    background: var(--card);
    box-shadow: 0 2px 6px rgba(0, 0, 0, 0.12);
  }
  .company-name {
    position: absolute;
    font-family: "Arimo", sans-serif;
    font-weight: 700;
    font-size: 52px;
    letter-spacing: 1px;
    line-height: 1;
    color: var(--ink);
  }
  .card-front .company-name { left: 160px; top: 180px; }
  .holder {
    position: absolute;
    left: 360px;
    top: 272px;
    font-family: "Arimo", sans-serif;
  }
  .holder-name {
    font-weight: 700;
    font-size: 25px;
    letter-spacing: 2px;
    color: var(--ink);
    text-transform: uppercase;
  }
  .holder-role {
    margin-top: 8px;
    font-size: 25px;
    letter-spacing: 1px;
    color: var(--ink-soft);
  }
  .card-back .company-name { left: 160px; top: 100px; }
  .address {
    position: absolute;
    left: 140px;
    top: 200px;
    font-family: "Arimo", sans-serif;
    font-size: 21px;
    line-height: 1.32;
    letter-spacing: 0.6px;
    color: var(--ink);
    font-style: normal;
  }
</style>
</head>
<body>
  <main class="sheet">
    <section class="card card-front" aria-label="Card front">
      <p class="company-name">VelmoraNet</p>
      <div class="holder">
        <p class="holder-name">Roshan Adeel</p>
        <p class="holder-role">Managing Director</p>
      </div>
    </section>
    <section class="card card-back" aria-label="Card back">
      <p class="company-name">VelmoraNet</p>
      <address class="address">
        Velmora Net Sdn. Bhd.<br>
        5th Floor, Block D<br>
        Wisma PLB No. 14<br>
        Jalan Seri Melor<br>
        50470 Kuala Lumpur, Malaysia
      </address>
    </section>
  </main>
</body>
</html>
```